Product Packaging design for Vaporizer Battery box

We are looking for product packaging for a new line of Vaporizer Batteries. These batteries are all sold in bundle packs, and each battery has its own cardboard box. For example, the bundle packs are simply bagged up packs of 2, 3, 5, 10, 25, etc.

There are 4 different kinds of batteries that we need the packaging designed for. I have attached templates of the packaging for your reference. I would like the packaging to be a similar theme across all the batteries to keep things consistent.

More details about the 4 batteries can be found on our website at:
http://www.tidemarkgoodsdepot.example/product-category/vape_batteries/
Password: tidevisit

Packing Requirements

The packaging should have our company logo somewhere on it. I have attached a few different variations/orientations of our logo for you to choose between.

The name of the battery
Tidemark Goods 1300mAh Variable Voltage Large Capacity Battery
Tidemark Goods 400mAh Slim Variable Voltage Battery
Tidemark Goods 280mAh Slim Automatic Buttonless Battery
Tidemark Goods 350mAh KOV Slim Battery

Company website www.TidemarkGoodsDepot.example

For the Tidemark Goods 350mAh KOV Slim Battery, have the product packaging color scheme be Black base with Gold wording/trim. This battery only comes in black and gold, so the packaging will match.

Make sure to use the proper packaging template for the batteries. There are only two templates and pretty much the only difference is the size. They both fold up to be a rectangle package.

Industry/Entity Type

Product

Colors

Designer to choose colors to be used in the design.

Requirements
Must have
• Packing Requirements
• The packaging should have our company logo somewhere on it. I have attached a few different variations/orientations of our logo for you to choose between.
• The name of the battery
• Tidemark Goods 1300mAh Variable Voltage Large Capacity Battery
• Tidemark Goods 400mAh Slim Variable Voltage Battery
• Tidemark Goods 280mAh Slim Automatic Buttonless Battery
• Tidemark Goods 350mAh KOV Slim Battery
• Company website www.TidemarkGoodsDepot.example
• For the Tidemark Goods 350mAh KOV Slim Battery, have the product packaging color scheme be Black base with Gold wording/trim. This battery only comes in black and gold, so the packaging will match.
• Make sure to use the proper packaging template for the batteries. There are only two templates and pretty much the only difference is the size. They both fold up to be a rectangle package.

```html
<!DOCTYPE html>
<html lang="en">
<head>
<meta charset="utf-8">
<title>Tidemark Goods 1300mAh Battery Box Dieline</title>
<link href="https://fonts.googleapis.com/css2?family=Questrial&display=swap" rel="stylesheet">
<style>
  :root {
    --stage-center: #f9a11b;
    --stage-mid: #f5791a;
    --stage-edge: #b2541a;
    --board-pattern: #242224;
    --board-flap: #221f21;
    --board-black: #050505;
    --trim-gold: #f7c31a;
    --ink-white: #ffffff;
  }
  html, body {
    margin: 0;
    padding: 0;
    width: 1200px;
    height: 900px;
    overflow: hidden;
  }
  body {
    background: radial-gradient(ellipse 70% 60% at 50% 45%, var(--stage-center) 0%, var(--stage-mid) 45%, var(--stage-edge) 100%);
    font-family: "Questrial", sans-serif;
  }
  .dieline {
    position: absolute;
    left: 0;
    top: 0;
    width: 1200px;
    height: 900px;
  }
  .spec-text {
    font-family: "Questrial", sans-serif;
    font-size: 10.5px;
    fill: var(--trim-gold);
    letter-spacing: 0.6px;
    text-anchor: middle;
  }
  .brand-name {
    font-family: "Questrial", sans-serif;
    fill: var(--trim-gold);
    text-anchor: middle;
  }
  .colour-option {
    font-family: "Questrial", sans-serif;
    font-size: 13px;
    fill: var(--ink-white);
  }
  .checkbox { fill: var(--ink-white); }
  .mark-badge { fill: var(--ink-white); }
</style>
</head>
<body>
<svg class="dieline" viewBox="0 0 1200 900" xmlns="http://www.w3.org/2000/svg">
  <!-- top tuck flap -->
  <path class="tuck-top" d="M487 158 V40 Q487 16 511 16 H556 Q580 16 580 40 V158 Z" fill="var(--board-flap)"/>
  <line x1="487" y1="65" x2="580" y2="65" stroke="#1a181a" stroke-width="1"/>
  <!-- top dust flaps -->
  <path class="dust-flap" d="M404 158 V114 H470 L486 150 V158 Z" fill="var(--board-flap)"/>
  <path class="dust-flap" d="M580 158 V150 L598 114 H662 V152 L672 158 Z" fill="var(--board-flap)"/>

  <!-- body: black base -->
  <rect class="body-base" x="394" y="158" width="372" height="586" fill="var(--board-black)"/>
  <!-- patterned upper area -->
  <g role="img" aria-label="Subtle dark geometric star pattern across the upper panels">
    <rect x="394" y="158" width="372" height="386" fill="var(--board-pattern)"/>
    <polygon points="486,544 533,576 580,544" fill="var(--board-pattern)"/>
  </g>
  <line class="panel-fold" x1="672" y1="158" x2="672" y2="544" stroke="#1c1a1c" stroke-width="1"/>
  <!-- gold chevron band -->
  <path class="gold-band" d="M394 544 H486 L533 576 L580 544 H766 V558 H580 L533 590 L486 558 H394 Z" fill="var(--trim-gold)"/>

  <!-- bottom dust flaps -->
  <path class="dust-flap" d="M404 744 V788 H470 L486 758 V744 Z" fill="var(--board-black)"/>
  <path class="dust-flap" d="M580 744 V758 L598 788 H662 V744 Z" fill="var(--board-black)"/>
  <!-- bottom tuck flap -->
  <path class="tuck-bottom" d="M673 744 V862 Q673 886 697 886 H742 Q766 886 766 862 V744 Z" fill="var(--board-black)"/>
  <line x1="673" y1="837" x2="766" y2="837" stroke="#1a1a1a" stroke-width="1"/>

  <!-- brand mark -->
  <g class="brand">
    <circle cx="533" cy="258" r="12" fill="var(--trim-gold)"/>
    <text class="brand-name" x="533" y="296" font-size="17">TIDEMARK</text>
    <text class="brand-name" x="533" y="309" font-size="7.5" letter-spacing="4">GOODS</text>
  </g>

  <!-- product specs -->
  <g class="specs">
    <text class="spec-text" x="533" y="618">1300mAh</text>
    <text class="spec-text" x="533" y="631">VARIABLE</text>
    <text class="spec-text" x="533" y="644">VOLTAGE</text>
    <text class="spec-text" x="533" y="669">LARGE</text>
    <text class="spec-text" x="533" y="682">CAPACITY</text>
    <text class="spec-text" x="533" y="695">BATTERY</text>
  </g>

  <!-- colour checklist -->
  <g class="colour-checklist">
    <text class="colour-option" transform="translate(607 649) rotate(-90)">green</text>
    <text class="colour-option" transform="translate(622 649) rotate(-90)">purple</text>
    <text class="colour-option" transform="translate(636 649) rotate(-90)">stainless</text>
    <text class="colour-option" transform="translate(651 649) rotate(-90)">Titanium</text>
    <rect class="checkbox" x="596" y="654" width="11" height="11"/>
    <rect class="checkbox" x="611" y="654" width="11" height="11"/>
    <rect class="checkbox" x="626" y="654" width="11" height="11"/>
    <rect class="checkbox" x="641" y="654" width="11" height="11"/>
    <text class="colour-option" transform="translate(607 709) rotate(-90)">Black</text>
    <text class="colour-option" transform="translate(622 709) rotate(-90)">white</text>
    <text class="colour-option" transform="translate(636 709) rotate(-90)">red</text>
    <text class="colour-option" transform="translate(651 709) rotate(-90)">blue</text>
    <rect class="checkbox" x="596" y="714" width="11" height="11"/>
    <rect class="checkbox" x="611" y="714" width="11" height="11"/>
    <rect class="checkbox" x="626" y="714" width="11" height="11"/>
    <rect class="checkbox" x="641" y="714" width="11" height="11"/>
  </g>

  <!-- compliance marks -->
  <g class="compliance-marks">
    <rect class="mark-badge" x="709" y="583" width="22" height="26" rx="3" role="img" aria-label="Conformity mark"/>
    <circle class="mark-badge" cx="721" cy="637" r="14" role="img" aria-label="Quality seal"/>
    <circle class="mark-badge" cx="721" cy="678" r="12" role="img" aria-label="Recycling mark"/>
    <rect class="mark-badge" x="702" y="698" width="36" height="26" rx="2" role="img" aria-label="Disposal mark"/>
  </g>
</svg>
</body>
</html>
```